Brindle Yard Care. The best in the biz

I run a lawn care service that offers full service mowing. 100% satisfaction guarantee. Fast, Friendly, quality service "I am your lawns best friend" I cut residential lawns. I offer a mow package that includes trimming, edging and clean up. Prices very from 20 dollars to 75. I want my logo to stand out. Free estimates

Target Market(s)

Home owners

Industry/Entity Type

Landscaping

Contact Information for Business Card

555-812-4473 tomvale48@quillmail.net Derek. Brindle Yard care

Colors
f37122
9bcb3c
cadf82

Requirements
Must have
• Company name.
• Phone number
• Email
• My services
• images
Nice to have
• A sun that is growing grass.
Should not have
• Incorrect information

```html
<!DOCTYPE html>
<html lang="en">
<head>
<meta charset="utf-8">
<title>Brindle Yard Care – Business Card</title>
<link rel="stylesheet" href="https://fonts.googleapis.com/css2?family=Open+Sans:wght@400;600&display=swap">
<style>
  :root {
    --backdrop: #111111;
    --card: #ffffff;
    --leaf: #9bcb3c;
    --leaf-soft: #cadf82;
    --brand-green: #1f9a3c;
    --accent: #f37122;
    --ink: #1d1d1d;
  }
  * { margin: 0; padding: 0; box-sizing: border-box; }
  html, body {
    width: 1200px; height: 902px; overflow: hidden;
    background: var(--backdrop);
    font-family: "Open Sans", Arial, sans-serif;
  }
  .business-card {
    position: absolute; left: 50px; top: 138px;
    width: 1100px; height: 625px;
    background: var(--card);
    overflow: hidden;
  }
  .card-art { position: absolute; inset: 0; }
  .brand {
    position: absolute; left: 55px; top: 112px;
    display: flex; align-items: center; gap: 16px;
  }
  .brand-dot {
    width: 60px; height: 60px; border-radius: 50%;
    background: var(--accent); flex: none;
  }
  .brand-name {
    color: var(--brand-green); font-weight: 600;
    font-size: 40px; line-height: 1; white-space: nowrap;
  }
  .owner { position: absolute; left: 402px; top: 268px; }
  .owner-name { color: var(--leaf); font-size: 36px; font-weight: 600; line-height: 1.1; }
  .owner-business { color: var(--accent); font-size: 26px; line-height: 1.2; }
  .contact { position: absolute; left: 511px; top: 386px; list-style: none; }
  .contact li {
    display: flex; align-items: center; gap: 12px;
    font-size: 27px; color: var(--ink); line-height: 36px;
  }
  .contact svg { width: 26px; height: 26px; flex: none; }
  .promise {
    position: absolute; right: 55px; top: 490px;
    text-align: right; color: var(--accent);
    font-size: 27px; line-height: 38px;
  }
</style>
</head>
<body>
  <div class="business-card">
    <svg class="card-art" width="1100" height="625" viewBox="0 0 1100 625">
      <defs>
        <linearGradient id="garden-top" x1="0" y1="0" x2="0" y2="1">
          <stop offset="0" stop-color="#8c8a84"/>
          <stop offset="0.3" stop-color="#4c6b3a"/>
          <stop offset="0.6" stop-color="#3f8a2a"/>
          <stop offset="1" stop-color="#5fae35"/>
        </linearGradient>
        <linearGradient id="garden-bottom" x1="0" y1="0" x2="0" y2="1">
          <stop offset="0" stop-color="#9a9890"/>
          <stop offset="0.45" stop-color="#6f7268"/>
          <stop offset="0.7" stop-color="#4f9a2e"/>
          <stop offset="1" stop-color="#3f8a2a"/>
        </linearGradient>
      </defs>
      <path class="band band-top" d="M540,0 C585,215 805,395 1100,401 L1100,0 Z" fill="var(--leaf)"/>
      <path class="photo photo-top" role="img" aria-label="Photo of a formal garden with clipped hedges in front of a timber-framed manor house" d="M556,0 C610,175 810,340 1100,351 L1100,0 Z" fill="url(#garden-top)"/>
      <path class="band band-bottom" d="M0,249 C255,222 478,330 560,625 L0,625 Z" fill="var(--leaf)"/>
      <path class="photo photo-bottom" role="img" aria-label="Photo of a stone castle entrance with round hedge gardens and a paved path" d="M0,288 C245,266 450,360 540,625 L0,625 Z" fill="url(#garden-bottom)"/>
    </svg>

    <div class="brand">
      <div class="brand-dot"></div>
      <div class="brand-name">Brindle Yard Care</div>
    </div>

    <div class="owner">
      <div class="owner-name">Derek</div>
      <div class="owner-business">Brindle Yard care</div>
    </div>

    <ul class="contact">
      <li>
        <svg viewBox="0 0 26 26" aria-hidden="true"><rect width="26" height="26" rx="3" fill="var(--accent)"/><path d="M6,11 Q13,4 20,11 L17,13 Q13,10 9,13 Z M8,15 H18 L19,20 H7 Z" fill="#fff"/></svg>
        <span>555-812-4473</span>
      </li>
      <li>
        <svg viewBox="0 0 26 26" aria-hidden="true"><rect width="26" height="26" rx="3" fill="var(--accent)"/><rect x="5" y="8" width="16" height="11" fill="none" stroke="#fff" stroke-width="1.6"/><path d="M5,8 L13,15 L21,8" fill="none" stroke="#fff" stroke-width="1.6"/></svg>
        <span>tomvale48@quillmail.net</span>
      </li>
    </ul>

    <div class="promise">
      <p>100% satisfaction guarantee</p>
      <p>Fast, Friendly, quality service</p>
    </div>
  </div>
</body>
</html>
```